Lunelle Rosa Hair Fancy Business Card’s

I want my business cards to be elite, original and very classy. I want the business cards to match the colors of my logo and to match the design posted. I would love the design of the picture I posted

I want the card all white .
The dripping on the top of the card I want it to match the pink color in my logo that’s also posted .
I need my logo on the business card !
I need my Instagram- @lunelle.rosa.hair__
And my phone number - 555 207 3962

Target Market(s)

My target market is young woman age 23 to older woman to the age of 65
I want both older and younger women to love my design . I don’t want any cheap looking business cards

Industry/Entity Type

Hair And Beauty

Contact Information for Business Card

Add my logo
Add my Instagram- @lunelle.rosa.hair__
My number - 555 207 3962
My website- www.lunellerosahair.example

Font styles to use
Serif
Script

Colors
ffffff
e667a6
e34298

Requirements
Must have
• The business cards must have my logo, my number , my website, and my Instagram!
Nice to have
• Nice to have glitter words that match my logo
• The business cards must look classy and mature
• I want them to be very unique!!
Should not have
• Should not have any colors that doesn’t match my logo ! This is very important! Please

```html
<!DOCTYPE html>
<html lang="en">
<head>
<meta charset="utf-8">
<title>Lunelle Rosa Hair — Business Card</title>
<link href="https://fonts.googleapis.com/css2?family=Cormorant+Garamond:wght@500;600&family=Montserrat:wght@400;500&display=swap" rel="stylesheet">
<style>
  :root {
    --stage: #2b2b2d;
    --card: #ffffff;
    --pink: #e34298;
    --pink-soft: #e667a6;
    --ink: #555559;
    --ink-light: #7a7a7e;
  }
  * { box-sizing: border-box; margin: 0; padding: 0; }
  html, body { width: 1200px; height: 852px; overflow: hidden; }
  body {
    background: var(--stage);
    position: relative;
    font-family: "Montserrat", sans-serif;
  }
  .card {
    position: absolute;
    width: 620px;
    height: 354px;
    background: var(--card);
    border-radius: 18px;
    box-shadow: 0 14px 34px rgba(0,0,0,0.45);
  }
  .card--front { left: 120px; top: 50px; }
  .card--back  { left: 460px; top: 448px; }

  .wordmark {
    font-family: "Cormorant Garamond", serif;
    font-weight: 600;
    color: var(--pink);
    text-align: center;
    line-height: 1;
    letter-spacing: 0.02em;
  }
  .card--front .wordmark {
    position: absolute;
    left: 0; right: 0; top: 150px;
    font-size: 52px;
  }
  .card--back .wordmark {
    position: absolute;
    left: 40px; top: 160px;
    width: 210px;
    font-size: 34px;
    text-align: center;
  }

  .divider {
    position: absolute;
    left: 282px; top: 96px;
    width: 1.5px; height: 150px;
    background: var(--pink);
  }

  .details {
    position: absolute;
    left: 310px; top: 100px;
  }
  .details__name {
    font-family: "Cormorant Garamond", serif;
    font-weight: 600;
    font-size: 27px;
    color: var(--pink);
    letter-spacing: 0.04em;
    text-transform: uppercase;
    line-height: 1;
  }
  .details__role {
    font-size: 14px;
    color: var(--ink-light);
    margin-top: 6px;
    margin-bottom: 18px;
  }
  .contact {
    list-style: none;
  }
  .contact li {
    display: flex;
    align-items: center;
    gap: 10px;
    font-size: 15px;
    color: var(--ink);
    margin-bottom: 8px;
  }
  .contact svg { width: 14px; height: 14px; flex: none; }
  .contact .accent { color: var(--pink); }
</style>
</head>
<body>
  <section class="card card--front" aria-label="Business card front">
    <div class="wordmark">Lunelle Rosa Hair</div>
  </section>

  <section class="card card--back" aria-label="Business card back">
    <div class="wordmark">Lunelle Rosa Hair</div>
    <div class="divider"></div>
    <div class="details">
      <div class="details__name">Dara Whitfield</div>
      <div class="details__role">Director</div>
      <ul class="contact">
        <li>
          <svg viewBox="0 0 24 24" aria-hidden="true"><path fill="#e34298" d="M6.6 10.8a15.1 15.1 0 0 0 6.6 6.6l2.2-2.2a1 1 0 0 1 1-.25 11.4 11.4 0 0 0 3.6.57 1 1 0 0 1 1 1V20a1 1 0 0 1-1 1A17 17 0 0 1 3 4a1 1 0 0 1 1-1h3.5a1 1 0 0 1 1 1c0 1.25.2 2.46.57 3.6a1 1 0 0 1-.25 1z"/></svg>
          555 207 3962
        </li>
        <li>
          <svg viewBox="0 0 24 24" aria-hidden="true"><circle cx="12" cy="12" r="9" fill="none" stroke="#e34298" stroke-width="2.4"/></svg>
          @lunelle.rosa.hair__
        </li>
        <li>
          <svg viewBox="0 0 24 24" aria-hidden="true"><g fill="none" stroke="#e34298" stroke-width="2"><circle cx="12" cy="12" r="9"/><ellipse cx="12" cy="12" rx="4" ry="9"/><path d="M3 12h18M5 7h14M5 17h14"/></g></svg>
          <span>www.<span class="accent">lunellerosahair</span>.example</span>
        </li>
      </ul>
    </div>
  </section>
</body>
</html>
```